Flat bootstrap design for existing site

I'm looking for a modern flat design based around an existing logo. This has to be a custom design (no external templates), and implemented into a bootstrap framework.

The logo is attached as 2 versions - choose whichever you want, that flows better with whatever design you choose.

Added screenshots of the existing site (currently using the default bootstrap layouts). Please make your designs around those pages in the screenshots (i.e. the homepage only has the postal code input and the header). The active page has 3 screenshots, because I wanted to illustrate the other states that would be visible (in the table rows).

This is a moving/junk removal website, just for some context.

Here's some example websites (flat designs) that I like, just to give you an idea of what I'm after.

https://www.plimvora.com/
https://dacklow.com/
https://trevanu.com/
https://quobrintal.com/en/

Coding

Coded - Design and coding required

Number of Pages Required

5+ page

Colors

Designer to choose colors to be used in the design.

Requirements
Must have
• It must be a modern/simple flat design, that is built around the existing logo (attached).
• It has to be implemented using bootstrap.

```html
<!DOCTYPE html>
<html lang="en">
<head>
<meta charset="utf-8">
<title>Truvane – Booking</title>
<link href="https://fonts.googleapis.com/css2?family=Raleway:wght@400;500;700&family=Roboto:wght@300;400&display=swap" rel="stylesheet">
<style>
  :root{
    --sky:#4bc8f5;
    --teal:#1c82a8;
    --panel:#f2f1ef;
    --panel-line:#dcdcdc;
    --ink:#2b2b2b;
    --muted:#555;
    --grid:#bcd6e6;
    --green:#3fb45c;
    --blue:#1fa6d6;
    --red:#e2574a;
    --nav-active:#6d6d6d;
    --footer:#000;
  }
  *{box-sizing:border-box;margin:0;padding:0}
  html,body{width:1168px;height:1200px;overflow:hidden;background:#fff;font-family:"Raleway",sans-serif;color:var(--ink)}
  .site-header{height:97px;background:var(--sky);position:relative}
  .brand{position:absolute;left:84px;top:30px;display:flex;align-items:center;gap:10px;color:#fff;font-weight:700;font-size:30px;letter-spacing:1px}
  .brand-dot{width:26px;height:26px;border-radius:50%;background:#fff}
  .main-nav{position:absolute;top:33px;left:608px;display:flex;align-items:center}
  .main-nav a{color:#fff;text-decoration:none;font-size:14px;height:28px;line-height:28px;margin-right:39px}
  .main-nav a.active{background:var(--nav-active);padding:0 21px;border-radius:2px;margin-right:22px;box-shadow:0 1px 3px rgba(0,0,0,.3)}
  .panel{position:absolute;left:84px;width:999px;background:var(--panel);border:1px solid var(--panel-line)}
  .panel-title{position:absolute;left:25px;font-size:22px;font-weight:500}
  .panel-rule{position:absolute;left:21px;right:20px;height:1px;background:#e0dfdc}
  .field-label{position:absolute;font-size:18px;font-weight:400}
  .field{position:absolute;background:#fff;border:1px solid #ccc;font-size:13px;text-transform:uppercase;color:var(--muted);padding-left:24px;letter-spacing:.3px}
  .field.single{height:48px;line-height:48px}
  .field.area{padding-top:17px}
  .field svg{position:absolute}
  .btn-update{position:absolute;left:824px;top:364px;width:152px;height:49px;background:var(--sky);color:#fff;font-size:18px;display:flex;align-items:center;justify-content:center;border-radius:2px}
  .notice{position:absolute;left:21px;top:89px;width:956px;height:48px;background:var(--sky);color:#fff;font-size:13px;line-height:48px;padding-left:21px;border-radius:2px}
  .drivers{position:absolute;left:22px;top:144px;width:954px;border-collapse:collapse;font-family:"Roboto",sans-serif;font-size:13px}
  .drivers th{background:var(--teal);color:#fff;font-weight:400;text-align:left;height:42px;padding:8px 0 0 24px;border-right:1px solid #3d9bbf}
  .drivers td{height:39px;padding-left:24px;border:1px solid var(--grid);color:#333}
  .drivers tr.blank td{height:41px}
  .status{display:inline-block;width:103px;height:26px;line-height:26px;text-align:center;color:#fff;border-radius:2px;font-size:13px;margin-left:-8px}
  .status.accepted{background:var(--green)}
  .status.sent{background:var(--blue)}
  .status.pending{background:var(--red)}
  .btn-pay{display:inline-block;width:103px;height:26px;line-height:26px;text-align:center;color:#fff;background:var(--sky);border-radius:2px;margin-left:6px}
  .site-footer{position:absolute;left:0;top:1113px;width:1168px;height:87px;background:var(--footer);color:#fff}
  .copyright{position:absolute;left:84px;top:35px;font-size:13px}
  .social{position:absolute;left:944px;top:31px;display:flex;gap:6px}
  .social span{width:23px;height:23px;border-radius:50%}
</style>
</head>
<body>
<header class="site-header">
  <div class="brand"><span class="brand-dot"></span>TRUVANE</div>
  <nav class="main-nav">
    <a class="active" href="#">BOOK</a>
    <a href="#">HOW IT WORKS</a>
    <a href="#">BECOME A DRIVER</a>
    <a href="#">SIGN IN</a>
  </nav>
</header>

<section class="panel" style="top:116px;height:455px">
  <h2 class="panel-title" style="top:36px">Booking Details</h2>
  <div class="panel-rule" style="top:77px"></div>
  <label class="field-label" style="left:23px;top:113px">Package selected:</label>
  <label class="field-label" style="left:509px;top:113px">Pick-up time selected:</label>
  <div class="field single" style="left:21px;top:150px;width:470px">Package 1
    <svg style="right:22px;top:18px" width="8" height="12" viewBox="0 0 8 12"><path d="M4 0L8 5H0zM4 12L0 7H8z" fill="#222"/></svg>
  </div>
  <div class="field single" style="left:507px;top:150px;width:470px">July 18 at 0:13 AM
    <svg style="right:22px;top:17px" width="12" height="13" viewBox="0 0 12 13"><rect x="0.5" y="2" width="11" height="10.5" fill="none" stroke="#222"/><rect x="0.5" y="2" width="11" height="3" fill="#222"/><rect x="2.5" y="0" width="1.5" height="3" fill="#222"/><rect x="8" y="0" width="1.5" height="3" fill="#222"/><path d="M3 7h6M3 9.5h6M5 5.5v6M7 5.5v6" stroke="#222" stroke-width=".8"/></svg>
  </div>
  <label class="field-label" style="left:23px;top:219px">Description:</label>
  <div class="field area" style="left:21px;top:256px;width:956px;height:91px">Package 1
    <svg style="right:14px;bottom:17px" width="11" height="11" viewBox="0 0 11 11"><path d="M1 10L10 1M6 1h4v4M1 6v4h4" fill="none" stroke="#888" stroke-width="1.3"/></svg>
  </div>
  <div class="btn-update">Update</div>
</section>

<section class="panel" style="top:603px;height:429px">
  <h2 class="panel-title" style="top:35px">Drivers in your area</h2>
  <div class="panel-rule" style="top:76px"></div>
  <div class="notice">Please stay on this page and be patient, while we contact the drivers and find you one ASAP.</div>
  <table class="drivers">
    <colgroup><col style="width:125px"><col style="width:215px"><col style="width:147px"><col style="width:138px"><col style="width:171px"><col style="width:158px"></colgroup>
    <tr><th>Name</th><th>Distance (km)</th><th>Agreed pick-up time</th><th></th><th></th><th style="border-right:0"></th></tr>
    <tr><td>Dorian Pell</td><td>4.04km away</td><td>July 17 at 4:13 am</td><td><span class="status accepted">Time accepted</span></td><td><span class="btn-pay">Make payment</span></td><td></td></tr>
    <tr><td>Marcus Wyeth</td><td>5.7km away</td><td>_</td><td><span class="status sent">Request sent</span></td><td></td><td></td></tr>
    <tr><td>Elian Corvo</td><td>11.13km away</td><td>_</td><td><span class="status sent">Request sent</span></td><td></td><td></td></tr>
    <tr><td>Rupert Halden</td><td>11.91km away</td><td>_</td><td><span class="status pending">Pending</span></td><td></td><td></td></tr>
    <tr class="blank"><td></td><td></td><td></td><td></td><td></td><td></td></tr>
  </table>
</section>

<footer class="site-footer">
  <p class="copyright">2017 © Truvane. All rights reserved.</p>
  <div class="social">
    <span style="background:#3b5998"></span>
    <span style="background:#4aa3df"></span>
    <span style="background:#e0463a"></span>
    <span style="background:#c4302b"></span>
    <span style="background:#b23a8d"></span>
  </div>
</footer>
</body>
</html>
```